Process Serving Company needs a letterhead design

Looking to have a letterhead designed for letters to attorneys advertising our business. We would like something eye catching but professional. Colors and logos are attached. Please add "Process Service and Attorney Support" near the logo or header

Target Market(s)

Attorneys

Font styles to use
Serif
Sans Serif

Colors
33a6d7
0255a3
85cae6
cee9f5
ecf7fb

```html
<!DOCTYPE html>
<html lang="en">
<head>
<meta charset="utf-8">
<title>Copperline Legal Couriers Letterhead</title>
<link rel="stylesheet" href="https://fonts.googleapis.com/css2?family=Source+Sans+3:wght@400;600&family=Roboto:wght@400&family=Arimo:wght@700&display=swap">
<style>
  :root {
    --brand-blue: #33a6d7;
    --brand-navy: #0255a3;
    --brand-sky: #85cae6;
    --brand-mist: #cee9f5;
    --brand-ice: #ecf7fb;
    --band-deep: #3b8ccd;
    --ink: #2b2b2b;
    --backdrop: #e6e6e6;
    --paper: #ffffff;
  }
  * { box-sizing: border-box; margin: 0; padding: 0; }
  html, body { width: 1059px; height: 1200px; overflow: hidden; background: var(--backdrop); }
  .letterhead {
    position: absolute; left: 104px; top: 0;
    width: 851px; height: 1200px;
    background: var(--paper); overflow: hidden;
  }
  .brand {
    position: absolute; left: 61px; top: 78px;
    display: flex; align-items: center; gap: 12px;
  }
  .brand-dot { width: 22px; height: 22px; border-radius: 50%; background: var(--brand-blue); flex: none; }
  .brand-name {
    font-family: "Source Sans 3", sans-serif; font-weight: 600; color: var(--brand-blue);
    font-size: 30px; line-height: 1;
  }
  .letter-body {
    position: absolute; left: 55px; top: 188px; width: 741px;
    font-family: "Source Sans 3", sans-serif; font-size: 17.4px; line-height: 22.3px;
    color: var(--ink); text-align: justify;
  }
  .salutation {
    font-family: "Arimo", sans-serif; font-weight: 700; font-size: 18.5px;
    color: #1a1a1a; margin-bottom: 27px;
  }
  .letter-body p { margin-bottom: 22.3px; }
  .signature {
    position: absolute; left: 55px; top: 822px; width: 133px; height: 65px;
    background: linear-gradient(90deg, #f4f4f4, #e9e9e9);
  }
  .footer-band { position: absolute; left: 0; bottom: 0; width: 851px; height: 140px; }
  .footer-web {
    position: absolute; left: 40px; top: 1150px;
    font-family: "Roboto", sans-serif; font-size: 12px; color: #fff; letter-spacing: 0.3px;
  }
  .contact-list {
    position: absolute; right: 46px; top: 1088px; list-style: none;
    font-family: "Roboto", sans-serif; font-size: 15px; color: #fff; text-align: right;
  }
  .contact-list li { display: flex; justify-content: flex-end; align-items: center; gap: 6px; height: 23.5px; }
  .contact-list li.address { margin-top: 7px; }
  .contact-icon { width: 17px; height: 17px; flex: none; }
</style>
</head>
<body>
<main class="letterhead">
  <header class="brand">
    <span class="brand-dot"></span>
    <span class="brand-name">Copperline Legal Couriers</span>
  </header>

  <section class="letter-body">
    <h1 class="salutation">Dear Mr. Carter,</h1>
    <p>Lorem Ipsum is simply dummy text of the printing and typesetting industry. Lorem Ipsum has been the industry's standard dummy text ever since the 1500s, when an unknown printer took a galley of type and scrambled it to make a type specimen book. It has survived not only five centuries, but also the leap into electronic typesetting, remaining essentially unchanged.</p>
    <p>The standard chunk of Lorem Ipsum used since the 1500s is reproduced below for those interested. Sections 1.10.32 and 1.10.33 from "de Finibus Bonorum et Malorum" by Cicero are also reproduced in their exact original form, accompanied by English versions from the 1914 translation by H. Rackham</p>
    <p>Lorem Ipsum is simply dummy text of the printing and typesetting industry. Lorem Ipsum has been the industry's standard dummy text ever since the 1500s, when an unknown printer took a galley of type and scrambled it to make a type specimen book. It has survived not only five centuries, but also the leap into electronic typesetting, remaining essentially unchanged. It was popularised in the</p>
    <p>The standard chunk of Lorem Ipsum used since the 1500s is reproduced below for those interested. Sections 1.10.32 and 1.10.33 from "de Finibus Bonorum et Malorum" by Cicero are also reproduced in their exact original form, accompanied by English versions from the 1914 translation by H. Rackham</p>
    <p>The standard chunk of Lorem Ipsum used since the 1500s is reproduced below for those interested. Sections 1.10.32 and 1.10.33 from "de Finibus Bonorum et Malorum" by Cicero are also reproduced in their exact original form.</p>
  </section>

  <div class="signature" role="img" aria-label="Handwritten signature of the sender"></div>

  <svg class="footer-band" viewBox="0 0 851 140" preserveAspectRatio="none" aria-hidden="true">
    <defs>
      <linearGradient id="bandFill" x1="0" y1="0" x2="1" y2="0">
        <stop offset="0" stop-color="#3b8ccd"/>
        <stop offset="0.6" stop-color="#6fbbe2"/>
        <stop offset="1" stop-color="#4a97d4"/>
      </linearGradient>
    </defs>
    <path d="M0 30 Q425 0 851 30 L851 140 L0 140 Z" fill="url(#bandFill)"/>
  </svg>

  <div class="footer-web">www.CopperlineCouriers.com</div>

  <ul class="contact-list">
    <li>555-201-4830
      <svg class="contact-icon" viewBox="0 0 20 20"><circle cx="10" cy="10" r="10" fill="#fff"/><path d="M5 8 Q10 4 15 8 L14 10 L12 9 L12 8 Q10 7 8 8 L8 9 L6 10 Z M6 11 H14 V14 H6 Z" fill="var(--band-deep)"/></svg>
    </li>
    <li>555-201-4831
      <svg class="contact-icon" viewBox="0 0 20 20"><circle cx="10" cy="10" r="10" fill="#fff"/><path d="M7 4 H12 V8 H7 Z M5 9 H15 V14 H5 Z" fill="var(--band-deep)"/></svg>
    </li>
    <li>Info@CopperlineCouriers.com
      <svg class="contact-icon" viewBox="0 0 20 20"><circle cx="10" cy="10" r="10" fill="#fff"/><path d="M5 7 H15 V14 H5 Z" fill="var(--band-deep)"/><path d="M5 7 L10 11 L15 7" stroke="#fff" fill="none"/></svg>
    </li>
    <li class="address">Canyon Street Lindale 4410 PO Box 52 Westvale 4410
      <svg class="contact-icon" viewBox="0 0 20 20"><circle cx="10" cy="10" r="10" fill="#fff"/><path d="M10 4 C7 4 6 6 6 8 C6 11 10 16 10 16 C10 16 14 11 14 8 C14 6 13 4 10 4 Z" fill="var(--band-deep)"/><circle cx="10" cy="8" r="1.6" fill="#fff"/></svg>
    </li>
  </ul>
</main>
</body>
</html>
```